Business Card Design Project

Mireille Castova logo on front of card with 'of Sydney' added in small font.
Back of card needs to include the following information :

"Pure pleasure for the discerning gentleman" (I may omit once I've seen the design)

mireillecastova.com.au

Contact by SMS or email only :

mireille@mireillecastova.com.au
Mobile : 0438 615 204 or + 61 438 615 204

Target Market(s)

Male professionals aged 20-60.

Industry/Entity Type

Business

Requirements
Must have
• Simple, bold, stylish and elegant.

```html
<!DOCTYPE html>
<html lang="en">
<head>
<meta charset="utf-8">
<title>Mireille Castova – Business Cards</title>
<link href="https://fonts.googleapis.com/css2?family=Questrial&family=Lobster+Two:ital,wght@1,700&display=swap" rel="stylesheet">
<style>
  :root {
    --backdrop: #3a3a3c;
    --card-white: #f4f4f5;
    --card-shade: #d9d9dc;
    --ink: #141414;
    --pattern-dark: #5a5a5e;
    --pattern-light: #a9a9ad;
    --accent-mauve: #b8a6bd;
    --logo-ink: #1d1a20;
  }
  html, body {
    margin: 0;
    padding: 0;
    width: 1200px;
    height: 900px;
    overflow: hidden;
    background: var(--backdrop);
  }
  .stage {
    position: relative;
    width: 1200px;
    height: 900px;
  }
  .card {
    position: absolute;
    width: 540px;
    height: 310px;
    border-radius: 22px;
    overflow: hidden;
    background: var(--card-white);
    box-shadow: 0 14px 30px rgba(0,0,0,0.45);
  }
  .card--front { left: 70px; top: 90px; }
  .card--back  { left: 590px; top: 500px; }
  .card__art {
    position: absolute;
    inset: 0;
    width: 100%;
    height: 100%;
  }
  .brand {
    position: absolute;
    text-align: center;
    color: var(--logo-ink);
    font-family: "Questrial", sans-serif;
  }
  .brand__name {
    display: block;
    font-size: 34px;
    letter-spacing: 1px;
    line-height: 1;
  }
  .brand__place {
    display: block;
    margin-top: 6px;
    font-size: 11px;
    letter-spacing: 0.5px;
  }
  .card--front .brand { left: 120px; top: 78px; width: 300px; }
  .card--back .brand  { left: 150px; top: 52px; width: 300px; }
  .tagline {
    position: absolute;
    right: 30px;
    top: 12px;
    font-family: "Lobster Two", cursive;
    font-style: italic;
    font-weight: 700;
    font-size: 15px;
    color: var(--ink);
    letter-spacing: 0.5px;
    white-space: nowrap;
  }
  .contact {
    position: absolute;
    font-family: "Questrial", sans-serif;
    font-size: 16px;
    line-height: 20px;
    color: var(--ink);
    letter-spacing: 0.6px;
    display: flex;
    align-items: center;
    white-space: nowrap;
  }
  .contact__icon {
    width: 18px;
    height: 18px;
    margin-right: 18px;
    flex: none;
    display: flex;
    align-items: center;
    justify-content: center;
    font-size: 15px;
  }
  .contact--phone { left: 88px; top: 172px; }
  .contact--or { left: 262px; top: 172px; }
  .contact--intl { left: 300px; top: 172px; }
  .contact--site { left: 88px; top: 214px; }
  .contact--mail { left: 88px; top: 254px; }
</style>
</head>
<body>
<main class="stage">

  <section class="card card--front" aria-label="Card front">
    <svg class="card__art" viewBox="0 0 540 310">
      <defs>
        <linearGradient id="patternTone" x1="0" y1="0" x2="1" y2="1">
          <stop offset="0" stop-color="var(--pattern-light)"/>
          <stop offset="1" stop-color="var(--pattern-dark)"/>
        </linearGradient>
        <linearGradient id="frontWhite" x1="0" y1="0" x2="0" y2="1">
          <stop offset="0" stop-color="#ffffff"/>
          <stop offset="1" stop-color="var(--card-shade)"/>
        </linearGradient>
      </defs>
      <rect class="pattern-field" width="540" height="310" fill="url(#patternTone)" role="img" aria-label="Black and white floral damask pattern"/>
      <path class="front-curve" d="M0,0 H540 V18 C450,175 230,215 0,185 Z" fill="url(#frontWhite)"/>
      <path d="M0,185 C230,215 450,175 540,18" fill="none" stroke="#ffffff" stroke-width="3" opacity="0.8"/>
    </svg>
    <div class="brand">
      <span class="brand__name">Mireille Castova</span>
      <span class="brand__place">of Sydney</span>
    </div>
  </section>

  <section class="card card--back" aria-label="Card back">
    <svg class="card__art" viewBox="0 0 540 310">
      <defs>
        <linearGradient id="patternToneB" x1="0" y1="0" x2="1" y2="1">
          <stop offset="0" stop-color="var(--pattern-light)"/>
          <stop offset="1" stop-color="var(--pattern-dark)"/>
        </linearGradient>
        <linearGradient id="backWhite" x1="0" y1="0" x2="1" y2="1">
          <stop offset="0" stop-color="#ffffff"/>
          <stop offset="1" stop-color="var(--card-shade)"/>
        </linearGradient>
      </defs>
      <rect width="540" height="310" fill="url(#backWhite)"/>
      <path class="pattern-corner" d="M0,0 H200 C145,8 80,45 0,140 Z" fill="url(#patternToneB)" role="img" aria-label="Floral damask pattern corner"/>
      <path d="M0,140 C80,45 145,8 200,0 H225 C160,12 85,70 0,190 Z" fill="var(--ink)"/>
      <path d="M200,0 C145,8 80,45 0,140" fill="none" stroke="var(--accent-mauve)" stroke-width="3"/>
      <path class="pattern-corner" d="M540,120 V310 H350 C440,295 510,235 540,120 Z" fill="url(#patternToneB)" role="img" aria-label="Floral damask pattern corner"/>
      <path d="M540,75 C510,210 440,290 335,310 H350 C440,295 510,235 540,120 Z" fill="var(--ink)"/>
    </svg>
    <div class="tagline">Pure pleasure for the discerning gentleman</div>
    <div class="brand">
      <span class="brand__name">Mireille Castova</span>
      <span class="brand__place">of Sydney</span>
    </div>
    <div class="contact contact--phone">
      <span class="contact__icon">
        <svg width="12" height="16" viewBox="0 0 12 16" aria-label="Mobile"><rect x="1" y="1" width="10" height="14" rx="2" fill="none" stroke="var(--ink)" stroke-width="1.4"/><line x1="4.5" y1="12.5" x2="7.5" y2="12.5" stroke="var(--ink)" stroke-width="1.2"/></svg>
      </span>
      0438 615 204
    </div>
    <div class="contact contact--or">or</div>
    <div class="contact contact--intl">+ 61 438 615 204</div>
    <div class="contact contact--site">
      <span class="contact__icon">
        <svg width="16" height="14" viewBox="0 0 16 14" aria-label="Website"><path d="M1,7 L8,1 L15,7 H13 V13 H3 V7 Z" fill="var(--ink)"/></svg>
      </span>
      mireillecastova.com.au
    </div>
    <div class="contact contact--mail">
      <span class="contact__icon">@</span>
      mireille@mireillecastova.com.au
    </div>
  </section>

</main>
</body>
</html>
```